Hartwell Estates Business Cards

I would like a business card that includes myself and my partner.
Includes: Logo, office #, email, website, our names, our numbers and possibly the address. I would also like the logo to be embossed and the card to be horizontal.
There is a photo of our yard signs to give you an idea of the colors of our business.

Target Market(s)

Everyone in real estate market.
We are in a rural area. Our clientele are from all socioeconomic backgrounds.

Industry/Entity Type

Real Estate Agent

Contact Information for Business Card

Company Name: Hartwell Estates
Our Names, Titles & Cell #'s : Dana Pembrook-Broker (555).317.6624, Marla Pembrook-Realtor (555).609.1385
Office #: (555).240.3918
Website: hartwellestates-demo.com
Joint Email: pembrook@hartwellestates-demo.com
Office Address: 418B W. Calloway Ave.
Cedar Bend, OK. 70913

Font styles to use
Serif

Requirements
Must have
• HORIZONTAL, Logo, Myself and my partners names, Our cell #'s, our office #, our website, our email address
Nice to have
• Embossed logo, office address, our titles.

```html
<!DOCTYPE html>
<html lang="en">
<head>
<meta charset="utf-8">
<title>Hartwell Estates Business Cards</title>
<link rel="stylesheet" href="https://fonts.googleapis.com/css2?family=Montserrat:wght@400;500;600&display=swap">
<style>
  :root {
    --backdrop: #ece8e2;
    --purple-light: #6a2496;
    --purple: #54137f;
    --purple-deep: #430b6a;
    --ink: #ffffff;
    --ink-soft: rgba(255,255,255,0.88);
    --emboss: rgba(255,255,255,0.13);
    --emboss-faint: rgba(255,255,255,0.07);
  }
  * { box-sizing: border-box; margin: 0; padding: 0; }
  html, body { width: 1200px; height: 1022px; overflow: hidden; }
  body {
    background: var(--backdrop);
    font-family: "Montserrat", sans-serif;
    color: var(--ink);
    position: relative;
  }
  .card {
    position: absolute;
    left: 250px;
    width: 700px;
    height: 400px;
    border-radius: 18px;
    background: linear-gradient(135deg, var(--purple-light) 0%, var(--purple) 50%, var(--purple-deep) 100%);
    box-shadow: 0 10px 28px rgba(40,10,60,0.25);
    overflow: hidden;
  }
  .card--front { top: 92px; }
  .card--back { top: 530px; }

  .brand-mark {
    position: absolute;
    left: 46px;
    top: 52px;
    display: flex;
    align-items: center;
    gap: 16px;
  }
  .brand-mark__dot {
    width: 54px; height: 54px;
    border-radius: 50%;
    background: var(--emboss);
  }
  .brand-mark__name {
    font-size: 40px;
    font-weight: 500;
    letter-spacing: 1px;
    color: var(--emboss);
  }

  .team {
    position: absolute;
    left: 46px;
    bottom: 48px;
    display: flex;
    flex-direction: column;
    gap: 26px;
  }
  .member__name { font-size: 28px; font-weight: 600; line-height: 1.1; }
  .member__title, .member__phone { font-size: 19px; font-weight: 400; color: var(--ink-soft); line-height: 1.3; }

  .back-mark {
    position: absolute;
    left: 40px;
    top: 40px;
    font-size: 48px;
    font-weight: 500;
    color: var(--emboss-faint);
    letter-spacing: 1px;
  }
  .contact {
    position: absolute;
    right: 40px;
    top: 150px;
    display: flex;
    flex-direction: column;
    align-items: flex-end;
    gap: 4px;
    font-size: 20px;
    font-weight: 400;
  }
  .contact__row { display: flex; align-items: center; gap: 14px; line-height: 1.35; }
  .contact__row--web strong { font-weight: 600; }
  .contact__icon { width: 16px; height: 16px; flex: none; }
  .contact__spacer { width: 16px; flex: none; }
</style>
</head>
<body>
  <section class="card card--front" aria-label="Card front">
    <div class="brand-mark">
      <span class="brand-mark__dot"></span>
      <span class="brand-mark__name">Hartwell Estates</span>
    </div>
    <div class="team">
      <div class="member">
        <div class="member__name">Dana Pembrook</div>
        <div class="member__title">Broker</div>
        <div class="member__phone">(555).317.6624</div>
      </div>
      <div class="member">
        <div class="member__name">Marla Pembrook</div>
        <div class="member__title">Realtor</div>
        <div class="member__phone">(555).609.1385</div>
      </div>
    </div>
  </section>

  <section class="card card--back" aria-label="Card back">
    <div class="back-mark">Hartwell Estates</div>
    <div class="contact">
      <div class="contact__row"><span>418B W. Calloway Ave.</span><span class="contact__spacer"></span></div>
      <div class="contact__row"><span>Cedar Bend, OK. 70913</span><span class="contact__spacer"></span></div>
      <div class="contact__row">
        <span>(555).240.3918</span>
        <svg class="contact__icon" viewBox="0 0 16 16" aria-hidden="true"><path d="M4 1.5 6 5 4.8 6.4c.8 1.9 2.4 3.6 4.8 4.8L11 10l3.5 2-1 2.5C7.5 14.5 1.5 8.5 1.5 2.5Z" fill="#fff"/></svg>
      </div>
      <div class="contact__row">
        <span>pembrook@hartwellestates-demo.com</span>
        <svg class="contact__icon" viewBox="0 0 16 16" aria-hidden="true"><rect x="1.5" y="3.5" width="13" height="9" rx="1" fill="none" stroke="#fff" stroke-width="1.5"/><path d="M2 4l6 5 6-5" fill="none" stroke="#fff" stroke-width="1.5"/></svg>
      </div>
      <div class="contact__row contact__row--web">
        <span>www.<strong>hartwellestates-demo</strong>.com</span>
        <svg class="contact__icon" viewBox="0 0 16 16" aria-hidden="true"><circle cx="8" cy="8" r="6.5" fill="none" stroke="#fff" stroke-width="1.4"/><ellipse cx="8" cy="8" rx="2.8" ry="6.5" fill="none" stroke="#fff" stroke-width="1.2"/><path d="M1.5 8h13" stroke="#fff" stroke-width="1.2"/></svg>
      </div>
    </div>
  </section>
</body>
</html>
```